Business card for Luxury Portable Restroom Trailer company

We are a Luxury Portable Restroom Trailer Company Called FALCRIDGE HIRES. Based in Orange County California. We provide portable restroom trailers for events, such as, Weddings, Concerts, Charity events, Sporting events, Tournaments, Corporate events, ect. We rent and Sell the Luxury restrooms. Our colors are white, grey, and Orange. As you will see in the logo we uploaded.
There are 2 people in the company so the names and titles will change for the 3 people but card will remain the same. Here is the information for each Person: Dwight Penner CFO 555 318-0476
next Person: Leon Marchetti VP 555 318-0476
Next Person: Owen Marchetti CEO 555 318-0476
Information to include on the card: Luxury Restroom Trailers Rental and Sales. Weddings, Concerts, Charity, Sporting and Corp. Events.

```html
<!DOCTYPE html>
<html lang="en">
<head>
<meta charset="utf-8">
<title>Falcridge Hires – Business Card</title>
<link href="https://fonts.googleapis.com/css2?family=Montserrat:wght@400;500;800&display=swap" rel="stylesheet">
<style>
  :root {
    --orange: #f26f2b;
    --grey: #58595b;
    --ink: #1f1f1f;
    --white: #ffffff;
    --backdrop: #2b2b2b;
  }
  * { box-sizing: border-box; margin: 0; padding: 0; }
  html, body {
    width: 1200px; height: 960px; overflow: hidden;
    background: var(--backdrop);
    font-family: "Montserrat", Arial, sans-serif;
  }
  .sheet {
    width: 1200px; height: 960px;
    display: flex; flex-direction: column;
    align-items: center; justify-content: center; gap: 36px;
  }
  .card {
    width: 760px; height: 434px;
    position: relative; overflow: hidden;
  }

  /* Front */
  .card--front {
    background: var(--orange);
    color: var(--white);
    display: flex; flex-direction: column;
    align-items: center; justify-content: center;
  }
  .brand-name {
    font-weight: 800; font-size: 64px; letter-spacing: 3px;
    line-height: 1; text-align: center;
  }
  .services {
    margin-top: 56px; text-align: center;
    font-weight: 500; font-size: 20px; line-height: 1.6;
  }
  .services .dot {
    display: inline-block; width: 11px; height: 11px;
    border-radius: 50%; background: var(--white);
    margin: 0 8px 2px 10px; vertical-align: middle;
  }

  /* Back */
  .card--back {
    background: var(--white);
    display: flex; align-items: center;
  }
  .brand-mark {
    width: 400px; display: flex; flex-direction: column;
    align-items: center; gap: 22px;
  }
  .brand-mark .ring {
    width: 120px; height: 120px; border-radius: 50%;
    border: 12px solid var(--orange);
  }
  .brand-mark .brand-name {
    color: var(--orange); font-size: 30px; letter-spacing: 2px;
  }
  .divider {
    width: 2px; height: 300px; background: var(--orange);
  }
  .contacts {
    padding-left: 34px;
    display: flex; flex-direction: column; gap: 18px;
  }
  .person-name {
    font-weight: 800; font-size: 24px; letter-spacing: 0.5px;
    color: var(--grey); text-transform: uppercase; line-height: 1.1;
  }
  .person-name .surname { color: var(--orange); }
  .person-title {
    font-size: 17px; color: var(--ink); margin-top: 3px; padding-left: 16px;
  }
  .person-phone {
    font-size: 17px; color: var(--ink); margin-top: 2px; padding-left: 16px;
    display: flex; align-items: center; gap: 8px;
  }
  .person-phone svg { width: 18px; height: 18px; fill: var(--orange); }
</style>
</head>
<body>
<main class="sheet">

  <section class="card card--front">
    <h1 class="brand-name">FALCRIDGE HIRES</h1>
    <p class="services">
      <span class="dot"></span>Luxury Restroom Trailers Rental and Sales<br>
      <span class="dot"></span>Weddings<span class="dot"></span>Concerts<span class="dot"></span>Charity<span class="dot"></span>Sporting and Corp<span class="dot"></span>Events
    </p>
  </section>

  <section class="card card--back">
    <div class="brand-mark">
      <div class="ring"></div>
      <p class="brand-name">FALCRIDGE HIRES</p>
    </div>
    <div class="divider"></div>
    <div class="contacts">
      <div class="person">
        <p class="person-name">Dwight <span class="surname">Penner</span></p>
        <p class="person-title">CFO</p>
        <p class="person-phone"><svg viewBox="0 0 24 24" aria-hidden="true"><path d="M6.6 10.8a15.1 15.1 0 0 0 6.6 6.6l2.2-2.2c.3-.3.7-.4 1-.2 1.1.4 2.3.6 3.6.6.6 0 1 .4 1 1V20c0 .6-.4 1-1 1A17 17 0 0 1 3 4c0-.6.4-1 1-1h3.5c.6 0 1 .4 1 1 0 1.3.2 2.5.6 3.6.1.3 0 .7-.2 1z"/></svg>555 318-0476</p>
      </div>
      <div class="person">
        <p class="person-name">Leon <span class="surname">Marchetti</span></p>
        <p class="person-title">VP</p>
        <p class="person-phone"><svg viewBox="0 0 24 24" aria-hidden="true"><path d="M6.6 10.8a15.1 15.1 0 0 0 6.6 6.6l2.2-2.2c.3-.3.7-.4 1-.2 1.1.4 2.3.6 3.6.6.6 0 1 .4 1 1V20c0 .6-.4 1-1 1A17 17 0 0 1 3 4c0-.6.4-1 1-1h3.5c.6 0 1 .4 1 1 0 1.3.2 2.5.6 3.6.1.3 0 .7-.2 1z"/></svg>555 318-0476</p>
      </div>
      <div class="person">
        <p class="person-name">Owen <span class="surname">Marchetti</span></p>
        <p class="person-title">CEO</p>
        <p class="person-phone"><svg viewBox="0 0 24 24" aria-hidden="true"><path d="M6.6 10.8a15.1 15.1 0 0 0 6.6 6.6l2.2-2.2c.3-.3.7-.4 1-.2 1.1.4 2.3.6 3.6.6.6 0 1 .4 1 1V20c0 .6-.4 1-1 1A17 17 0 0 1 3 4c0-.6.4-1 1-1h3.5c.6 0 1 .4 1 1 0 1.3.2 2.5.6 3.6.1.3 0 .7-.2 1z"/></svg>555 318-0476</p>
      </div>
    </div>
  </section>

</main>
</body>
</html>
```